Business card design for sustainable building and development company

Need a business card design for a new sustainable building and real estate development company in the San Francisco Bay area. Name of company is "Tovrin Advisors, LLC" and we provide "Sustainable building, energy and development services" for residential and non residential projects. We'd like the following colors used but not all area required: green, gray, blue. Design should communicate innovation, professionalism and sustainability. Our current website is www.tovrin-advisors.example. Another possible design idea is to have the following listed on the back of the card:
Certified: VERN QS, Eco Marker Rater, DOLM Rater, Terravue Inspector, KSO TQ Building Analyst. Its not a must but could be text that could be used for back of card. Overall, we are open to a simple, clean design and or one with more text than usual for a card.

Industry/Entity Type

Real Estate

Contact Information for Business Card

Name on card: Mark J. Halvik
Title for Name: Principal + Founder
Phone: 555.814.0627
Email: mhalvik@tovrin-advisors.example
Website: www.tovrin-advisors.example

Also, please add the following for address:
San Francisco, California

Requirements
Nice to have
• If you can integrate the outline of a skyline on the backside of the card and if it looks good, I would like to see the design
Should not have
• a barcode;

```html
<!DOCTYPE html>
<html lang="en">
<head>
<meta charset="utf-8">
<title>Tovrin Advisors — Business Card</title>
<link rel="stylesheet" href="https://fonts.googleapis.com/css2?family=Montserrat:wght@500;700&family=Open+Sans:wght@400&display=swap">
<style>
  :root {
    --green: #6abb44;
    --ink: #111111;
    --paper: #ffffff;
    --backdrop: #e4e4e4;
    --ghost: #f1f0ef;
  }
  html, body {
    margin: 0;
    padding: 0;
    width: 1200px;
    height: 1000px;
    overflow: hidden;
    background: var(--backdrop);
  }
  .canvas {
    position: relative;
    width: 1200px;
    height: 1000px;
  }
  .card {
    position: absolute;
    background: var(--paper);
    overflow: hidden;
    font-family: "Open Sans", sans-serif;
  }
  .card--front { left: 42px; top: 26px; width: 780px; height: 454px; }
  .card--back { left: 372px; top: 516px; width: 786px; height: 448px; }

  .certifications {
    position: absolute;
    left: 16px; top: 12px;
    margin: 0;
    font-size: 16.5px;
    color: var(--green);
    white-space: nowrap;
  }
  .brand {
    position: absolute;
    left: 72px; top: 156px;
    display: flex;
    align-items: center;
    gap: 22px;
  }
  .brand__dot {
    width: 160px; height: 160px;
    border-radius: 50%;
    background: var(--green);
    flex: none;
  }
  .brand__name {
    margin: 0;
    font-family: "Montserrat", sans-serif;
    font-weight: 700;
    font-size: 54px;
    line-height: 1;
    color: var(--green);
    letter-spacing: -0.5px;
  }
  .brand__tagline {
    margin: 8px 0 0 2px;
    font-family: "Montserrat", sans-serif;
    font-weight: 500;
    font-size: 15.5px;
    color: var(--ink);
    text-transform: uppercase;
    white-space: nowrap;
  }
  .band {
    position: absolute;
    left: 0; right: 0; bottom: 0;
    background: var(--green);
  }
  .card--front .band { height: 34px; }
  .card--back .band { height: 96px; }
  .tab {
    position: absolute;
    background: var(--green);
    border-radius: 20px 20px 0 0;
    color: var(--paper);
  }
  .location {
    left: 325px; top: 398px;
    width: 405px; height: 56px;
    margin: 0;
    font-size: 27px;
    letter-spacing: 1px;
    text-align: center;
    line-height: 52px;
  }
  .backdrop-ring {
    position: absolute;
    left: 0; top: 0;
  }
  .holder {
    position: absolute;
    left: 324px; top: 260px;
    margin: 0;
    font-size: 55px;
    font-weight: 400;
    color: var(--ink);
    line-height: 1;
  }
  .contact {
    left: 286px; top: 330px;
    width: 450px; height: 118px;
    margin: 0;
    padding: 14px 0 0 39px;
    box-sizing: border-box;
    list-style: none;
    font-size: 21.5px;
    line-height: 31px;
  }
  .contact__key { display: inline-block; width: 46px; }
</style>
</head>
<body>
<main class="canvas">
  <section class="card card--front" aria-label="Card front">
    <p class="certifications">Certified: VERN QS, Eco Marker Rater, DOLM Rater, Terravue Inspector, KSO TQ Building Analyst</p>
    <div class="brand">
      <span class="brand__dot" aria-hidden="true"></span>
      <div>
        <h1 class="brand__name">Tovrin Advisors</h1>
        <p class="brand__tagline">Sustainable Building, Energy &amp; Development Services</p>
      </div>
    </div>
    <div class="band"></div>
    <p class="tab location">San Francisco, California</p>
  </section>

  <section class="card card--back" aria-label="Card back">
    <svg class="backdrop-ring" width="786" height="448" aria-hidden="true">
      <circle cx="272" cy="186" r="208" fill="none" stroke="var(--ghost)" stroke-width="34"/>
    </svg>
    <h2 class="holder">Mark J. Halvik</h2>
    <div class="band"></div>
    <ul class="tab contact">
      <li><span class="contact__key">[t]</span>555.814.0627</li>
      <li><span class="contact__key">[e]</span>mhalvik@tovrin-advisors.example</li>
      <li><span class="contact__key">[w]</span>www.tovrin-advisors.example</li>
    </ul>
  </section>
</main>
</body>
</html>
```